Business card design

I am open to ideas. I was thinking of a vertical design, turning the name 90 degrees and placing it on the left edge, then some clipped portion of the fabulous tree with contact info on the bottom -- special emphasis on Web address:WhimBeads.comFor All Your Beading Needs121 E. Cotati AveCotati, CA 94931(707) 664-8343

```html
<!DOCTYPE html>
<html lang="en">
<head>
<meta charset="utf-8">
<title>Fern Glass Co — Business Card</title>
<link rel="stylesheet" href="https://fonts.googleapis.com/css2?family=Roboto+Slab:wght@400&display=swap">
<style>
  :root {
    --backdrop: #8c8c8c;
    --card-light: #ffffff;
    --card-dark: #161616;
    --art-placeholder: #eeeeee;
    --web-yellow: #f5c30f;
    --phone-red: #e6202a;
    --address-purple: #8b64c6;
    --tagline-green: #8fcc2c;
    --brand-ink: #1c1c1c;
    --rule: #e9e9e9;
  }
  html, body {
    margin: 0;
    width: 1200px;
    height: 1200px;
    overflow: hidden;
    background: var(--backdrop);
  }
  .card {
    position: absolute;
    left: 300px;
    top: 110px;
    width: 600px;
    height: 980px;
    font-family: "Roboto Slab", Georgia, serif;
    box-shadow: 0 4px 14px rgba(0,0,0,0.25);
  }
  .card-top {
    position: absolute;
    inset: 0 0 auto 0;
    height: 466px;
    background: var(--card-light);
  }
  .tree-art {
    position: absolute;
    left: 145px;
    top: 68px;
    width: 350px;
    height: 250px;
    background: var(--art-placeholder);
  }
  .brand-name {
    position: absolute;
    left: 0;
    right: 0;
    top: 340px;
    margin: 0;
    text-align: center;
    font-size: 44px;
    line-height: 1;
    font-weight: 400;
    color: var(--brand-ink);
  }
  .card-bottom {
    position: absolute;
    inset: 466px 0 0 0;
    background: var(--card-dark);
  }
  .line {
    position: absolute;
    left: 0;
    right: 0;
    margin: 0;
    text-align: center;
    font-weight: 400;
    line-height: 1;
    white-space: nowrap;
  }
  .web { top: 92px; font-size: 38px; color: var(--web-yellow); }
  .phone { top: 143px; font-size: 33px; color: var(--phone-red); }
  .address-1 { top: 240px; font-size: 32px; color: var(--address-purple); }
  .address-2 { top: 284px; font-size: 32px; color: var(--address-purple); }
  .tagline { top: 396px; font-size: 32px; color: var(--tagline-green); }
  .divider {
    position: absolute;
    left: 222px;
    width: 156px;
    height: 2px;
    background: var(--rule);
  }
  .divider-1 { top: 205px; }
  .divider-2 { top: 362px; }
</style>
</head>
<body>
  <article class="card">
    <section class="card-top">
      <div class="tree-art" role="img" aria-label="Illustration of a tree with rainbow-coloured leaves and a rope swing"></div>
      <p class="brand-name">Fern Glass Co</p>
    </section>
    <section class="card-bottom">
      <p class="line web">FernGlassco.com</p>
      <p class="line phone">(707) 555-0192</p>
      <div class="divider divider-1"></div>
      <p class="line address-1">348 W. Brindle Ave</p>
      <p class="line address-2">Alderton, CA 94990</p>
      <div class="divider divider-2"></div>
      <p class="line tagline">For All Your Beading Needs</p>
    </section>
  </article>
</body>
</html>
```